Commercial Loan Originator Business Card (CHANGE COLORS SCHEME)

CHANGE COLOR SCHEME - SAME DESIGN

Name Marlene Agate
Title Commercial Loan Originator
Office (800) 417-2906 x68
Direct (240) 615-2043
Email freshgreens4life@quillbox.example

Name Dale Morrow
Office (800) 417-2906 x70
Direct (410) 392-5184
Email d.morthehomeguy@quillbox.example

Name Leonard Vasko
Office (800) 417-2906 x71
Direct (215) 463-0712
Email l.vasko41@quillbox.example

Name Gwen Halsey
Office (800) 417-2906 x
Direct (202) 548-1370
Email ghalsey63@quillbox.example

Name Mirna Ashby
Office (800) 417-2906 x72
Direct (240) 871-4526
Email tristatehomelending@quillbox.example

```html
<!DOCTYPE html>
<html lang="en">
<head>
<meta charset="utf-8">
<title>Mirna Ashby – Commercial Loan Originator</title>
<link rel="stylesheet" href="https://fonts.googleapis.com/css2?family=Montserrat:wght@400;700&display=swap">
<style>
  :root {
    --page: #1b1b1c;
    --brand-main: #1d5a46;
    --brand-accent: #c9a24a;
    --paper: #ffffff;
    --portrait-dark: #2a2424;
    --portrait-warm: #8a5a44;
  }
  * { margin: 0; padding: 0; box-sizing: border-box; }
  html, body {
    width: 1200px; height: 1059px; overflow: hidden;
    background: var(--page);
    font-family: "Montserrat", Arial, sans-serif;
  }
  .business-card {
    position: absolute; left: 80px; top: 234px;
    width: 1040px; height: 590px;
    border-radius: 26px; overflow: hidden;
    background: var(--brand-main);
  }
  .card-shapes { position: absolute; inset: 0; }
  .portrait {
    position: absolute; left: 680px; top: 116px;
    width: 340px; height: 474px;
    border-radius: 140px 140px 0 0;
    background: linear-gradient(180deg, var(--portrait-warm) 0%, var(--portrait-dark) 45%, #151212 100%);
  }
  .identity { position: absolute; left: 60px; top: 258px; color: var(--paper); }
  .person-name { font-weight: 700; font-size: 50px; letter-spacing: 0.5px; line-height: 1; text-transform: uppercase; }
  .person-title { font-weight: 400; font-size: 28px; margin-top: 10px; letter-spacing: 0.3px; }
  .contact-list { position: absolute; left: 60px; top: 385px; list-style: none; color: var(--paper); }
  .contact-item { display: flex; align-items: center; height: 57px; font-size: 29px; letter-spacing: 0.2px; white-space: nowrap; }
  .contact-item.email { font-size: 24px; letter-spacing: 0; }
  .contact-icon { width: 22px; height: 22px; margin-right: 13px; flex: none; fill: var(--brand-accent); }
</style>
</head>
<body>
  <div class="business-card">
    <svg class="card-shapes" viewBox="0 0 1040 590" width="1040" height="590" aria-hidden="true">
      <path d="M345 0 H1040 V494 C 900 486, 745 462, 640 395 C 500 310, 400 170, 345 0 Z" fill="var(--paper)"/>
    </svg>
    <div class="portrait" role="img" aria-label="Portrait photo of the loan originator, seated in a black top"></div>

    <div class="identity">
      <h1 class="person-name">Mirna Ashby</h1>
      <p class="person-title">Commercial Loan Originator</p>
    </div>

    <ul class="contact-list">
      <li class="contact-item">
        <svg class="contact-icon" viewBox="0 0 24 24"><path d="M6.6 10.8a15.1 15.1 0 0 0 6.6 6.6l2.2-2.2a1 1 0 0 1 1-.25 11.4 11.4 0 0 0 3.6.57 1 1 0 0 1 1 1V20a1 1 0 0 1-1 1A17 17 0 0 1 3 4a1 1 0 0 1 1-1h3.5a1 1 0 0 1 1 1c0 1.25.2 2.45.57 3.57a1 1 0 0 1-.25 1z"/></svg>
        (800) 417-2906 x72
      </li>
      <li class="contact-item">
        <svg class="contact-icon" viewBox="0 0 24 24"><path d="M7 1h10a2 2 0 0 1 2 2v18a2 2 0 0 1-2 2H7a2 2 0 0 1-2-2V3a2 2 0 0 1 2-2zm0 3v14h10V4zm5 15.3a1.2 1.2 0 1 0 0 2.4 1.2 1.2 0 0 0 0-2.4z"/></svg>
        (240) 871-4526
      </li>
      <li class="contact-item email">
        <svg class="contact-icon" viewBox="0 0 24 24"><path d="M2 5h20v14H2zm2 2v.4l8 5.2 8-5.2V7l-8 5.2zm0 2.8V17h16V9.8l-8 5.2z"/></svg>
        tristatehomelending@quillbox.example
      </li>
    </ul>
  </div>
</body>
</html>
```